Landing Page and Logo for Auto-Blogging Platform

I created a platform that allows users to start a blog for their business, hobby, charity, etc. I need a landing page where users can learn about the platform, benefits of consistent blogging, SEO value, plans/pricing, etc. The landing page needs to have multiple call to action buttons encouraging the visitor to register/sign up for a free trial.

In addition to the landing page, I need a page for users to establish the settings for their blog. This page should be a fairly simple form, intended for the user to enter a few details to set up their blog:
1. Name of Blog
2. Up to 10 topics and/or keywords the blog should focus on
3. Theme: Color-scheme and logo upload for blog.

I have attached the specifications of the platform's functionality so you can better understand how it works, plans/pricing, etc.

I also need a logo for the business. The name of the platform is PostNook.

Target Market(s)

Website owners, bloggers, business owners

Industry/Entity Type

Technology, Internet, web design

Coding

Coded - Design and coding required

Number of Pages Required

2 page

Colors
0054AA
0677BA
7BADD7
CADEEF
E8F1F8
0094D4
00A9DD
6FCCEA
C7EBF8
E9F6FB

Requirements
Must have
• Eye-catching design but fairly light on content (keep it simple and brief.)
Nice to have
• Eye-catching yet simple design, clean and easy to understand what we are offering.
Should not have
• Too much “wordy” and confusing content.

```html
<!DOCTYPE html>
<html lang="en">
<head>
<meta charset="utf-8">
<title>PostNook – Automate Your Blog Posting with AI</title>
<link rel="stylesheet" href="https://fonts.googleapis.com/css2?family=Kanit:wght@300;400;500&family=Roboto:wght@400;500;700&display=swap">
<style>
:root{
  --navy:#0054AA;
  --blue:#0677BA;
  --bright:#0094D4;
  --sky:#00A9DD;
  --light:#6FCCEA;
  --pale:#E8F1F8;
  --ice:#E9F6FB;
  --ink:#1d1d1f;
  --text:#4a4a4a;
  --footer:#1c1d1f;
  --white:#ffffff;
}
*{margin:0;padding:0;box-sizing:border-box}
html,body{width:1200px;height:3507px;overflow:hidden;background:var(--white)}
body{position:relative;font-family:"Roboto",sans-serif;color:var(--text)}
.abs{position:absolute}
.heading{font-family:"Kanit",sans-serif;font-weight:400;text-transform:uppercase;letter-spacing:.5px}

/* header */
.site-header{position:absolute;left:0;top:0;width:1200px;height:84px;background:var(--white)}
.brand{position:absolute;display:flex;align-items:center;gap:8px;font-family:"Kanit",sans-serif;font-weight:400;color:var(--navy);text-transform:uppercase}
.brand-dot{border:3px solid currentColor;border-radius:50%}
.site-header .brand{left:145px;top:18px;font-size:29px}
.site-header .brand-dot{width:40px;height:40px}
.nav{position:absolute;top:32px;left:447px;display:flex;gap:29px;font-size:14px;font-weight:500;color:#222;text-transform:uppercase}
.nav .active{color:var(--bright);position:relative}
.nav .active::before{content:"";position:absolute;left:-2px;right:-2px;top:-32px;height:3px;background:var(--bright)}
.search{position:absolute;left:882px;top:32px}
.btn-outline{position:absolute;border:2px solid var(--navy);border-radius:30px;color:var(--ink);font-weight:700;font-size:13px;display:flex;align-items:center;justify-content:center;text-transform:uppercase;background:var(--white)}

/* hero */
.hero{position:absolute;left:0;top:84px;width:1200px;height:560px;background:linear-gradient(100deg,#3a3a36 0%,#6c6a60 35%,#8c8f86 55%,#44504a 80%,#2a302d 100%)}
.hero-shade{position:absolute;inset:0;background:linear-gradient(180deg,rgba(0,0,0,0) 45%,rgba(0,0,0,.55) 100%)}
.hero h1{position:absolute;left:120px;top:402px;font-size:36px;line-height:44px;color:var(--white)}
.hero p{position:absolute;left:579px;top:406px;width:502px;font-size:14px;line-height:24px;color:var(--white)}
.slider-btn{position:absolute;left:1134px;width:30px;height:30px;border-radius:50%;background:var(--white);display:flex;align-items:center;justify-content:center}

/* about */
.about-photo{position:absolute;left:167px;top:744px;width:409px;height:409px;border-radius:50%;background:radial-gradient(circle at 55% 40%,#e7c7a4 0%,#d39a4c 35%,#8a6b52 70%,#5b4a3e 100%)}
.about-ring{position:absolute;left:150px;top:727px}
.about h2{position:absolute;left:631px;top:772px;font-size:48px;color:var(--ink)}
.about p{position:absolute;left:631px;width:424px;font-size:14px;line-height:24px;text-align:justify;color:#555}

/* benefits */
.benefits{position:absolute;left:0;top:1263px;width:1200px;height:458px;background:linear-gradient(120deg,#0a4fae 0%,var(--navy) 45%,#0f5fc0 100%)}
.benefits h2{position:absolute;left:143px;top:1365px;font-size:40px;color:var(--white)}
.benefit-list{position:absolute;left:143px;top:1428px;list-style:none;color:var(--white);font-size:18px}
.benefit-list li{height:32px;display:flex;align-items:center;gap:13px}
.benefit-photo{position:absolute;left:667px;top:1364px;width:396px;height:426px;border:8px solid var(--navy);border-radius:40px 0 40px 40px;background:linear-gradient(160deg,#aebfbe 0%,#7d8c86 40%,#6b6052 75%,#4e4a45 100%)}
.benefit-arc{position:absolute;left:968px;top:1340px}

/* pricing */
.pricing{position:absolute;left:0;top:1721px;width:1200px;height:745px;background:#0989d0}
.pricing h2{position:absolute;left:0;width:1200px;top:1830px;text-align:center;font-size:40px;color:var(--white)}
.plan{position:absolute;top:1898px;width:277px;height:443px;background:#45aee3;border-radius:4px;color:var(--white);text-align:center}
.plan.featured{background:var(--white);height:450px;color:var(--ink);box-shadow:0 8px 24px rgba(0,0,0,.18)}
.plan-pill{display:inline-block;margin-top:31px;padding:0 18px;height:36px;line-height:36px;border-radius:20px;background:var(--blue);color:var(--white);font-size:16px;font-weight:500}
.plan-title{margin-top:18px;font-size:28px;font-weight:700}
.plan-sub{margin-top:6px;font-size:13px}
.plan.featured .plan-sub{color:var(--blue)}
.plan-price{margin-top:14px;height:54px;line-height:54px;font-size:29px;font-weight:700;background:rgba(255,255,255,.12)}
.plan.featured .plan-price{background:var(--pale);color:var(--blue)}
.plan-list{list-style:none;text-align:left;margin:16px 0 0 33px;font-size:17px}
.plan-list li{height:32px;display:flex;align-items:center;gap:15px}
.plan.featured .plan-list li{color:#555}

/* steps */
.steps h2{position:absolute;left:0;width:1200px;top:2555px;text-align:center;font-size:41px;color:var(--ink)}
.steps .lead{position:absolute;left:0;width:1200px;top:2613px;text-align:center;font-size:20px;color:#222}
.step-ring{position:absolute;width:216px;height:216px;border:2px solid var(--blue);border-radius:50%;display:flex;flex-direction:column;align-items:center;justify-content:flex-start;padding-top:56px;text-align:center;font-size:12px;line-height:18px;color:#333}
.step-ring svg{margin-bottom:12px}
.step-num{position:absolute;width:44px;height:44px;margin-left:-22px;border-radius:50%;background:var(--navy);color:var(--white);font-size:12px;font-weight:500;display:flex;align-items:center;justify-content:center}

/* footer */
.site-footer{position:absolute;left:0;top:3138px;width:1200px;height:369px;background:linear-gradient(180deg,#232427 0%,var(--footer) 100%);color:var(--white)}
.site-footer .brand{left:185px;top:3226px;font-size:44px;color:var(--white)}
.site-footer .brand-dot{width:60px;height:60px}
.social{position:absolute;top:3325px;width:32px;height:32px;border-radius:50%;border:1.5px solid var(--white)}
.social.filled{background:var(--white)}
.footer-title{position:absolute;top:3220px;font-family:"Kanit",sans-serif;font-size:21px;font-weight:400}
.footer-list{position:absolute;top:3262px;list-style:none;font-size:16px}
.footer-list li{height:24px;display:flex;align-items:center;gap:12px}
.contact-list li{height:48px;align-items:flex-start;gap:14px}
.footer-rule{position:absolute;left:144px;top:3426px;width:912px;height:1px;background:#4a4b4e}
.copyright{position:absolute;left:0;width:1200px;top:3459px;text-align:center;font-size:13px}
</style>
</head>
<body>

<header class="site-header">
  <div class="brand"><span class="brand-dot"></span>PostNook</div>
  <nav class="nav">
    <span class="active">Home</span><span>About Us</span><span>Services</span><span>Blog</span><span>Contact</span>
  </nav>
  <svg class="search" width="14" height="14" viewBox="0 0 14 14"><circle cx="6" cy="6" r="4.5" fill="none" stroke="#222" stroke-width="2"/><line x1="9.3" y1="9.3" x2="13" y2="13" stroke="#222" stroke-width="2"/></svg>
  <a class="btn-outline" style="left:927px;top:22px;width:128px;height:38px">Get Quote</a>
</header>

<section class="hero">
  <div class="abs" role="img" aria-label="Woman with glasses working on a laptop by a window" style="inset:0"></div>
  <div class="hero-shade"></div>
  <h1 class="heading">Automate your blog<br>posting with AI</h1>
  <p>Transform your blogging experience with our AI-powered platform that not only generates and optimizes content tailored to your audience but also continuously learns and adapts to deliver smarter insights, ensuring your voice stands out in a crowded digital landscape.</p>
  <div class="slider-btn" style="top:221px"><svg width="10" height="6"><path d="M1 5 5 1 9 5" fill="none" stroke="#333" stroke-width="1.4"/></svg></div>
  <div class="slider-btn" style="top:262px"><svg width="10" height="6"><path d="M1 1 5 5 9 1" fill="none" stroke="#333" stroke-width="1.4"/></svg></div>
</section>

<section class="about">
  <svg class="about-ring" width="450" height="450" viewBox="0 0 450 450"><path d="M222 5 A220 220 0 0 0 222 445" fill="none" stroke="#0a8bd3" stroke-width="16"/></svg>
  <div class="about-photo" role="img" aria-label="Smiling woman in an orange sweater typing on a laptop"></div>
  <h2 class="heading">About Us</h2>
  <p style="top:840px">There needs to be a super-admin panel where platform owner/administrator can see users, their activity, manage user access, etc.</p>
  <p style="top:936px">Each user will have a dashboard where they control their settings such as account information, billing, view blog posts, view blog post topics, etc. From this dashboard, the user can customize the “look and feel” of their blog including theme, hero banner, header, footer, logo, color scheme, etc.</p>
  <a class="btn-outline" style="left:631px;top:1076px;width:224px;height:38px;border-color:var(--blue);font-size:13px">Sign up for a free trial</a>
</section>

<section class="benefits"></section>
<section class="pricing"></section>

<h2 class="heading benefits-title abs" style="left:143px;top:1365px;font-size:40px;color:#fff">Our Benefits</h2>
<ul class="benefit-list">
  <li><svg width="15" height="15" viewBox="0 0 16 16"><circle cx="8" cy="8" r="8" fill="#fff"/><path d="M4.5 8.3 7 10.6 11.5 5.6" fill="none" stroke="#0054AA" stroke-width="2"/></svg>Lorem ipsum dolor sit amet, consectetur adipiscing</li>
  <li><svg width="15" height="15" viewBox="0 0 16 16"><circle cx="8" cy="8" r="8" fill="#fff"/><path d="M4.5 8.3 7 10.6 11.5 5.6" fill="none" stroke="#0054AA" stroke-width="2"/></svg>Duis aute irure dolor in reprehenderit in voluptate velit</li>
  <li><svg width="15" height="15" viewBox="0 0 16 16"><circle cx="8" cy="8" r="8" fill="#fff"/><path d="M4.5 8.3 7 10.6 11.5 5.6" fill="none" stroke="#0054AA" stroke-width="2"/></svg>Excepteur sint occaecat cupidatat non proident, sunt</li>
  <li><svg width="15" height="15" viewBox="0 0 16 16"><circle cx="8" cy="8" r="8" fill="#fff"/><path d="M4.5 8.3 7 10.6 11.5 5.6" fill="none" stroke="#0054AA" stroke-width="2"/></svg>Lorem ipsum dolor sit amet, consectetur adipiscing</li>
  <li><svg width="15" height="15" viewBox="0 0 16 16"><circle cx="8" cy="8" r="8" fill="#fff"/><path d="M4.5 8.3 7 10.6 11.5 5.6" fill="none" stroke="#0054AA" stroke-width="2"/></svg>Duis aute irure dolor in reprehenderit in voluptate velit</li>
  <li><svg width="15" height="15" viewBox="0 0 16 16"><circle cx="8" cy="8" r="8" fill="#fff"/><path d="M4.5 8.3 7 10.6 11.5 5.6" fill="none" stroke="#0054AA" stroke-width="2"/></svg>Excepteur sint occaecat cupidatat non proident, sunt</li>
</ul>
<svg class="benefit-arc" width="120" height="120" viewBox="0 0 120 120"><path d="M8 4 A56 56 0 0 1 72 100" fill="none" stroke="#fff" stroke-width="16"/></svg>
<div class="benefit-photo" role="img" aria-label="Smiling grey-haired man in a blazer holding a tablet"></div>

<h2 class="heading" style="position:absolute;left:0;width:1200px;top:1830px;text-align:center;font-size:40px;color:#fff">Choose Pricing Plan</h2>

<div class="plan" style="left:144px">
  <span class="plan-pill">Base Plan</span>
  <div class="plan-title">1 blog post</div>
  <div class="plan-sub">(up to 2,000 words)</div>
  <div class="plan-price">$9.99/mo</div>
  <ul class="plan-list">
    <li><svg width="14" height="14" viewBox="0 0 16 16"><circle cx="8" cy="8" r="8" fill="#0054AA"/><path d="M4.5 8.3 7 10.6 11.5 5.6" fill="none" stroke="#fff" stroke-width="2"/></svg>Lorem ipsum dolor sit</li>
    <li><svg width="14" height="14" viewBox="0 0 16 16"><circle cx="8" cy="8" r="8" fill="#0054AA"/><path d="M4.5 8.3 7 10.6 11.5 5.6" fill="none" stroke="#fff" stroke-width="2"/></svg>Duis aute irure dolor</li>
    <li><svg width="14" height="14" viewBox="0 0 16 16"><circle cx="8" cy="8" r="8" fill="#0054AA"/><path d="M4.5 8.3 7 10.6 11.5 5.6" fill="none" stroke="#fff" stroke-width="2"/></svg>Excepteur sint occa</li>
    <li><svg width="14" height="14" viewBox="0 0 16 16"><circle cx="8" cy="8" r="8" fill="#0054AA"/><path d="M4.5 8.3 7 10.6 11.5 5.6" fill="none" stroke="#fff" stroke-width="2"/></svg>Lorem ipsum dolor sit</li>
    <li><svg width="14" height="14" viewBox="0 0 16 16"><circle cx="8" cy="8" r="8" fill="#0054AA"/><path d="M4.5 8.3 7 10.6 11.5 5.6" fill="none" stroke="#fff" stroke-width="2"/></svg>Duis aute irure dolor</li>
    <li><svg width="14" height="14" viewBox="0 0 16 16"><circle cx="8" cy="8" r="8" fill="#0054AA"/><path d="M4.5 8.3 7 10.6 11.5 5.6" fill="none" stroke="#fff" stroke-width="2"/></svg>Excepteur sint occa</li>
  </ul>
</div>
<div class="plan featured" style="left:461px">
  <span class="plan-pill">Premium Plan</span>
  <div class="plan-title">1 blog post</div>
  <div class="plan-sub">(up to 2,000 words)</div>
  <div class="plan-price">$14.99/mo</div>
  <ul class="plan-list">
    <li><svg width="14" height="14" viewBox="0 0 16 16"><circle cx="8" cy="8" r="8" fill="#0054AA"/><path d="M4.5 8.3 7 10.6 11.5 5.6" fill="none" stroke="#fff" stroke-width="2"/></svg>Lorem ipsum dolor sit</li>
    <li><svg width="14" height="14" viewBox="0 0 16 16"><circle cx="8" cy="8" r="8" fill="#0054AA"/><path d="M4.5 8.3 7 10.6 11.5 5.6" fill="none" stroke="#fff" stroke-width="2"/></svg>Duis aute irure dolor</li>
    <li><svg width="14" height="14" viewBox="0 0 16 16"><circle cx="8" cy="8" r="8" fill="#0054AA"/><path d="M4.5 8.3 7 10.6 11.5 5.6" fill="none" stroke="#fff" stroke-width="2"/></svg>Excepteur sint occa</li>
    <li><svg width="14" height="14" viewBox="0 0 16 16"><circle cx="8" cy="8" r="8" fill="#0054AA"/><path d="M4.5 8.3 7 10.6 11.5 5.6" fill="none" stroke="#fff" stroke-width="2"/></svg>Lorem ipsum dolor sit</li>
    <li><svg width="14" height="14" viewBox="0 0 16 16"><circle cx="8" cy="8" r="8" fill="#0054AA"/><path d="M4.5 8.3 7 10.6 11.5 5.6" fill="none" stroke="#fff" stroke-width="2"/></svg>Duis aute irure dolor</li>
    <li><svg width="14" height="14" viewBox="0 0 16 16"><circle cx="8" cy="8" r="8" fill="#0054AA"/><path d="M4.5 8.3 7 10.6 11.5 5.6" fill="none" stroke="#fff" stroke-width="2"/></svg>Excepteur sint occa</li>
  </ul>
</div>
<div class="plan" style="left:777px">
  <span class="plan-pill">Ultimate Plan</span>
  <div class="plan-title">1 blog post</div>
  <div class="plan-sub">(up to 3,000 words)</div>
  <div class="plan-price">$24.99/mo</div>
  <ul class="plan-list">
    <li><svg width="14" height="14" viewBox="0 0 16 16"><circle cx="8" cy="8" r="8" fill="#0054AA"/><path d="M4.5 8.3 7 10.6 11.5 5.6" fill="none" stroke="#fff" stroke-width="2"/></svg>Lorem ipsum dolor sit</li>
    <li><svg width="14" height="14" viewBox="0 0 16 16"><circle cx="8" cy="8" r="8" fill="#0054AA"/><path d="M4.5 8.3 7 10.6 11.5 5.6" fill="none" stroke="#fff" stroke-width="2"/></svg>Duis aute irure dolor</li>
    <li><svg width="14" height="14" viewBox="0 0 16 16"><circle cx="8" cy="8" r="8" fill="#0054AA"/><path d="M4.5 8.3 7 10.6 11.5 5.6" fill="none" stroke="#fff" stroke-width="2"/></svg>Excepteur sint occa</li>
    <li><svg width="14" height="14" viewBox="0 0 16 16"><circle cx="8" cy="8" r="8" fill="#0054AA"/><path d="M4.5 8.3 7 10.6 11.5 5.6" fill="none" stroke="#fff" stroke-width="2"/></svg>Lorem ipsum dolor sit</li>
    <li><svg width="14" height="14" viewBox="0 0 16 16"><circle cx="8" cy="8" r="8" fill="#0054AA"/><path d="M4.5 8.3 7 10.6 11.5 5.6" fill="none" stroke="#fff" stroke-width="2"/></svg>Duis aute irure dolor</li>
    <li><svg width="14" height="14" viewBox="0 0 16 16"><circle cx="8" cy="8" r="8" fill="#0054AA"/><path d="M4.5 8.3 7 10.6 11.5 5.6" fill="none" stroke="#fff" stroke-width="2"/></svg>Excepteur sint occa</li>
  </ul>
</div>
<a class="btn-outline" style="left:537px;top:2331px;width:126px;height:36px;border-color:var(--blue);font-size:12px">Choose Plan</a>

<section class="steps">
  <h2 class="heading">How to set up the auto-blog</h2>
  <p class="lead">The blog topics can be created using any of these methods:</p>
  <svg class="abs" style="left:0;top:2650px" width="1200" height="180" viewBox="0 0 1200 180">
    <g stroke="#0054AA" stroke-width="1.5" stroke-dasharray="2 4" fill="none">
      <line x1="600" y1="6" x2="600" y2="83"/>
      <line x1="236" y1="83" x2="964" y2="83"/>
      <line x1="236" y1="83" x2="236" y2="160"/>
      <line x1="478" y1="83" x2="478" y2="160"/>
      <line x1="719" y1="83" x2="719" y2="160"/>
      <line x1="964" y1="83" x2="964" y2="160"/>
    </g>
    <g fill="#0677BA"><circle cx="236" cy="83" r="7"/><circle cx="478" cy="83" r="7"/><circle cx="719" cy="83" r="7"/><circle cx="964" cy="83" r="7"/></g>
  </svg>

  <div class="step-ring" style="left:128px;top:2824px">
    <svg width="60" height="56" viewBox="0 0 60 56" fill="none" stroke="#0677BA" stroke-width="2"><circle cx="22" cy="20" r="14"/><circle cx="22" cy="20" r="6"/><path d="M34 30v-8a3 3 0 0 1 6 0v12h4a4 4 0 0 1 4 4v12H36l-6-10"/></svg>
    Select frequency of<br>Automated Blog Posts (daily,<br>weekly, or monthly)
  </div>
  <div class="step-ring" style="left:370px;top:2824px">
    <svg width="56" height="56" viewBox="0 0 56 56" fill="none" stroke="#0677BA" stroke-width="2"><rect x="8" y="4" width="32" height="44" rx="3"/><line x1="16" y1="14" x2="32" y2="14"/><line x1="16" y1="22" x2="32" y2="22"/><line x1="16" y1="30" x2="28" y2="30"/><path d="M36 46 50 30l4 4-14 16h-4z"/></svg>
    Name your blog
  </div>
  <div class="step-ring" style="left:611px;top:2824px">
    <svg width="56" height="56" viewBox="0 0 56 56" fill="none" stroke="#0677BA" stroke-width="2"><rect x="4" y="4" width="10" height="10" rx="2"/><rect x="4" y="20" width="10" height="10" rx="2"/><rect x="4" y="36" width="10" height="10" rx="2"/><rect x="20" y="4" width="30" height="10" rx="2"/><path d="M28 46V24a3 3 0 0 1 6 0v10h6a4 4 0 0 1 4 4v14H30"/></svg>
    Select your blog topics (or<br>let AI choose them for you)
  </div>
  <div class="step-ring" style="left:856px;top:2824px">
    <svg width="56" height="56" viewBox="0 0 56 56" fill="none" stroke="#0677BA" stroke-width="2"><rect x="4" y="16" width="44" height="30" rx="2"/><line x1="4" y1="40" x2="48" y2="40"/><path d="M22 46v6h8v-6"/><path d="M30 28 48 6l4 4-18 22h-4z"/><line x1="12" y1="26" x2="24" y2="26"/><line x1="12" y1="32" x2="22" y2="32"/></svg>
    Go do something else<br>and let AI do all your<br>blogging for you!
  </div>

  <div class="step-num" style="left:236px;top:2810px">01</div>
  <div class="step-num" style="left:478px;top:2810px">02</div>
  <div class="step-num" style="left:719px;top:2810px">03</div>
  <div class="step-num" style="left:964px;top:2810px">04</div>
</section>

<footer class="site-footer"></footer>
<div class="brand" style="left:185px;top:3226px;font-size:44px;color:#fff"><span class="brand-dot" style="width:60px;height:60px"></span>PostNook</div>
<span class="social" style="left:271px"></span>
<span class="social filled" style="left:315px"></span>

<div class="footer-title" style="left:542px;color:#fff">Quick Links</div>
<ul class="footer-list" style="left:545px;color:#fff">
  <li><svg width="11" height="11" viewBox="0 0 12 12"><circle cx="6" cy="6" r="5" fill="none" stroke="#0094D4" stroke-width="1.5"/><path d="M5 3.5 7.5 6 5 8.5" fill="none" stroke="#0094D4" stroke-width="1.5"/></svg>Home</li>
  <li><svg width="11" height="11" viewBox="0 0 12 12"><circle cx="6" cy="6" r="5" fill="none" stroke="#0094D4" stroke-width="1.5"/><path d="M5 3.5 7.5 6 5 8.5" fill="none" stroke="#0094D4" stroke-width="1.5"/></svg>About</li>
  <li><svg width="11" height="11" viewBox="0 0 12 12"><circle cx="6" cy="6" r="5" fill="none" stroke="#0094D4" stroke-width="1.5"/><path d="M5 3.5 7.5 6 5 8.5" fill="none" stroke="#0094D4" stroke-width="1.5"/></svg>Services</li>
  <li><svg width="11" height="11" viewBox="0 0 12 12"><circle cx="6" cy="6" r="5" fill="none" stroke="#0094D4" stroke-width="1.5"/><path d="M5 3.5 7.5 6 5 8.5" fill="none" stroke="#0094D4" stroke-width="1.5"/></svg>Blog</li>
  <li><svg width="11" height="11" viewBox="0 0 12 12"><circle cx="6" cy="6" r="5" fill="none" stroke="#0094D4" stroke-width="1.5"/><path d="M5 3.5 7.5 6 5 8.5" fill="none" stroke="#0094D4" stroke-width="1.5"/></svg>Contact</li>
</ul>

<div class="footer-title" style="left:782px;color:#fff">Contact Us</div>
<ul class="footer-list contact-list" style="left:785px;color:#fff">
  <li><svg width="12" height="16" viewBox="0 0 12 16"><path d="M6 15C2 10 1 8 1 6a5 5 0 0 1 10 0c0 2-1 4-5 9z" fill="#0094D4"/><circle cx="6" cy="6" r="2" fill="#1c1d1f"/></svg>123, Lorem ipsum dolor sit</li>
  <li><svg width="14" height="14" viewBox="0 0 14 14"><path d="M3 1h3l1 3-2 1.5a8 8 0 0 0 3.5 3.5L10 7l3 1v3a2 2 0 0 1-2 2A11 11 0 0 1 1 3a2 2 0 0 1 2-2z" fill="#0094D4"/></svg>+1 888 888 8888</li>
  <li><svg width="15" height="12" viewBox="0 0 15 12"><rect x="0.5" y="0.5" width="14" height="11" rx="1" fill="#0094D4"/><path d="M1 1.5 7.5 7 14 1.5" fill="none" stroke="#1c1d1f" stroke-width="1.2"/></svg>info@companyname</li>
</ul>

<div class="footer-rule"></div>
<div class="copyright" style="color:#fff">© &nbsp;Copyrights 2024 | All Rights Reserved</div>

</body>
</html>
```